4 x Florist Footpath Signage Boards that are consistant with each other for a modern florist

Eye catching, easy to read. little bit floral.
See example attached for wording. We are a modern florist in a country town.
This will be out on the street and needs to stand out!!

The Signage Panels
1. Valentines Day - 14th Feb
2. Workshop Signage boards - see attached example
3. Mothers Day Signage Board - 'Treat mum this Mothers Day'
4. We Are Open

Attached is a copy of the design guidelines and the template. the base of the sign is white.

Target Market(s)

Modern

Industry/Entity Type

Florist

Font styles to use
Sans Serif

Colors
eea4c8
f59296
ffffff
757575

Requirements
Must have
• flowers
• weddings
• giftware
• workshops
• flowers make people happy
• lucywrenblooms.co.nz
Nice to have
• Logo
• little bit of floral or greenery
• my shop is modem and industrial
Should not have
• Needs to be able to read easy

```html
<!DOCTYPE html>
<html lang="en">
<head>
<meta charset="utf-8">
<title>Lucy Wren Blooms – Mothers Day footpath board</title>
<link href="https://fonts.googleapis.com/css2?family=Kaushan+Script&family=Noto+Serif:wght@400;700&family=Montserrat:wght@400&display=swap" rel="stylesheet">
<style>
  :root {
    --page: #ececec;
    --board: #e9fbf7;
    --magenta: #c218c0;
    --blue: #1f8fc2;
    --ink: #222222;
    --gold: #c9a86a;
    --petal: #f4a9b8;
    --leaf: #8d9a63;
    --leaf-soft: #b8c49a;
    --slot-line: #9a9a9a;
  }
  * { margin: 0; padding: 0; box-sizing: border-box; }
  html, body {
    width: 720px; height: 1200px; overflow: hidden;
    background: var(--page);
  }
  .board {
    position: absolute; left: 30px; top: 162px;
    width: 660px; height: 877px;
    background: var(--board);
    box-shadow: 0 8px 24px rgba(0,0,0,0.25);
    overflow: hidden;
  }
  .florals { position: absolute; inset: 0; }
  .hanging-slot {
    position: absolute; left: 278px; top: 31px;
    width: 104px; height: 28px;
    border-radius: 14px;
    background: #ffffff;
    border: 2px solid var(--slot-line);
  }
  .brand-name {
    position: absolute; left: 380px; top: 236px; width: 220px;
    text-align: center;
    font-family: "Montserrat", sans-serif;
    font-weight: 400; font-size: 17px; line-height: 1.35;
    letter-spacing: 4px; color: var(--gold);
  }
  .headline {
    position: absolute; left: 0; width: 100%;
    font-family: "Kaushan Script", cursive;
    white-space: nowrap;
  }
  .headline-treat { top: 372px; left: 66px; font-size: 84px; color: var(--magenta); }
  .headline-this { top: 470px; left: 300px; font-size: 46px; color: var(--blue); }
  .headline-day { top: 512px; left: 74px; font-size: 82px; color: var(--blue); }
  .shop-box {
    position: absolute; left: 34px; top: 672px;
    width: 590px; height: 70px;
    border: 1.5px solid var(--magenta);
    border-radius: 6px;
  }
  .shop-label {
    position: absolute; left: 158px; top: -20px;
    padding: 0 10px;
    background: var(--board);
    font-family: "Noto Serif", serif; font-weight: 700;
    font-size: 28px; line-height: 36px;
    color: var(--magenta);
  }
  .shop-url {
    position: absolute; left: 0; right: 0; top: 18px;
    text-align: center;
    font-family: "Noto Serif", serif; font-weight: 400;
    font-size: 30px; letter-spacing: 2px;
    color: var(--ink);
  }
</style>
</head>
<body>
  <main class="board">
    <svg class="florals" width="660" height="877" viewBox="0 0 660 877">
      <defs>
        <radialGradient id="bloom-top" cx="0.25" cy="0.2" r="0.8">
          <stop offset="0" stop-color="#f4a9b8"/>
          <stop offset="0.45" stop-color="#b4b78a"/>
          <stop offset="1" stop-color="#9aa874" stop-opacity="0.15"/>
        </radialGradient>
        <radialGradient id="bloom-bottom" cx="0.8" cy="0.85" r="0.8">
          <stop offset="0" stop-color="#f4a9b8"/>
          <stop offset="0.5" stop-color="#a8b587"/>
          <stop offset="1" stop-color="#a8b587" stop-opacity="0.1"/>
        </radialGradient>
        <linearGradient id="sprig-side" x1="0" y1="0" x2="0" y2="1">
          <stop offset="0" stop-color="#f4a9b8" stop-opacity="0.7"/>
          <stop offset="1" stop-color="#9aa874" stop-opacity="0.6"/>
        </linearGradient>
      </defs>
      <path role="img" aria-label="Pink blossoms and olive greenery in the top left corner"
        fill="url(#bloom-top)"
        d="M0 0 H640 C600 60 520 40 450 60 C400 80 340 110 300 170 C280 240 240 290 160 330 C110 380 90 460 60 560 L0 600 Z"/>
      <path role="img" aria-label="Pink rosebuds and sprigs along the right edge"
        fill="url(#sprig-side)"
        d="M660 380 C620 420 590 470 600 520 C610 580 580 620 540 650 C580 660 620 640 660 620 Z"/>
      <path role="img" aria-label="Pink blossoms and greenery in the bottom right corner"
        fill="url(#bloom-bottom)"
        d="M660 877 H220 C250 840 300 810 380 790 C450 770 520 740 580 700 C610 680 640 660 660 650 Z"/>
    </svg>

    <div class="hanging-slot"></div>

    <div class="brand-name">LUCY WREN<br>BLOOMS</div>

    <h1 class="headline headline-treat">Treat mum</h1>
    <p class="headline headline-this">this</p>
    <p class="headline headline-day">Mothers Day</p>

    <div class="shop-box">
      <span class="shop-label">SHOP ONLINE</span>
      <p class="shop-url">LucyWrenBlooms.co.nz</p>
    </div>
  </main>
</body>
</html>
```